Business Card Design

New business card design

Target Market(s)

Residential & Commercial Property Managers

Industry/Entity Type

Plumbing Services

Contact Information for Business Card

Name - Rowan Keddle, title - Director, Phone Number - 0431 286 517, email - rowan@tbk-plumbing.com.au, Company ABN - 73 215 904 386,

Font styles to use
Sans Serif

Colors
0054AA
0677BA
7BADD7
CADEEF
E8F1F8

```html
<!DOCTYPE html>
<html lang="en">
<head>
<meta charset="utf-8">
<title>TBK Plumbing Services – Business Card</title>
<link rel="stylesheet" href="https://fonts.googleapis.com/css2?family=Poppins:wght@300;400;500&display=swap">
<style>
  :root {
    --backdrop: #222222;
    --paper: #ffffff;
    --navy: #1b232c;
    --aqua: #29a8e0;
    --taupe: #6e6558;
    --taupe-light: #857c70;
    --text-light: #ffffff;
  }
  * { margin: 0; padding: 0; box-sizing: border-box; }
  html, body {
    width: 1200px; height: 780px; overflow: hidden;
    background: var(--backdrop);
    font-family: "Poppins", Arial, sans-serif;
  }
  .canvas {
    position: relative; width: 1200px; height: 780px;
  }
  .card {
    position: absolute; top: 235px;
    width: 540px; height: 310px;
    overflow: hidden;
  }
  .card--front { left: 30px; background: var(--paper); }
  .card--back { left: 630px; background: var(--taupe); }

  /* wordmark */
  .wordmark {
    position: absolute; text-align: center;
  }
  .wordmark__name {
    display: block;
    font-weight: 300; font-size: 104px; line-height: 1;
    letter-spacing: 4px;
  }
  .wordmark__tagline {
    display: block;
    font-weight: 400; font-size: 11px;
    letter-spacing: 11px; margin-top: 4px;
  }
  .card--front .wordmark { left: 190px; top: 22px; width: 300px; }
  .card--front .wordmark__name { color: var(--navy); }
  .card--front .wordmark__tagline { color: var(--taupe); }
  .card--back .wordmark { left: 110px; top: 80px; width: 320px; }
  .card--back .wordmark__name { color: var(--taupe-light); }
  .card--back .wordmark__tagline { color: var(--taupe-light); }

  /* bands */
  .band { position: absolute; top: 180px; height: 78px; }
  .band--name { left: 0; width: 255px; background: var(--navy); }
  .band--contact { left: 255px; width: 245px; background: var(--taupe); }
  .accent-dot {
    position: absolute; left: 226px; top: 187px;
    width: 64px; height: 64px; border-radius: 50%;
    background: var(--aqua); border: 3px solid var(--paper);
  }

  .person {
    position: absolute; right: 58px; top: 12px; text-align: right;
  }
  .person__name {
    color: var(--aqua); font-size: 24px; line-height: 1.15;
  }
  .person__name b { font-weight: 500; }
  .person__name span { font-weight: 300; }
  .person__title {
    color: var(--text-light); font-size: 12px; font-weight: 400;
  }

  .contact-list {
    position: absolute; left: 44px; top: 13px; list-style: none;
  }
  .contact-list li {
    display: flex; align-items: center; gap: 6px;
    color: var(--text-light); font-size: 11px; font-weight: 400;
    line-height: 17px; white-space: nowrap;
  }
  .contact-list svg { width: 10px; height: 10px; flex: none; }

  .abn {
    position: absolute; left: 70px; top: 272px;
    color: var(--aqua); font-size: 12px; font-weight: 400;
  }
</style>
</head>
<body>
<main class="canvas">
  <section class="card card--front" aria-label="Business card front">
    <div class="wordmark">
      <span class="wordmark__name">tbk</span>
      <span class="wordmark__tagline">plumbing services</span>
    </div>

    <div class="band band--name">
      <div class="person">
        <p class="person__name"><b>Rowan</b> <span>Keddle</span></p>
        <p class="person__title">Director</p>
      </div>
    </div>
    <div class="band band--contact">
      <ul class="contact-list">
        <li>
          <svg viewBox="0 0 10 10"><path d="M2 1 L4 1 L4.6 3 L3.4 4 Q4.5 6 6 6.6 L7 5.4 L9 6 L9 8 Q9 9 8 9 Q1 8.5 1 2 Q1 1 2 1 Z" fill="#29a8e0"/></svg>
          0431 286 517
        </li>
        <li>
          <svg viewBox="0 0 10 10"><circle cx="5" cy="5" r="4" fill="none" stroke="#29a8e0" stroke-width="1"/><path d="M1 5 H9 M5 1 Q2.5 5 5 9 M5 1 Q7.5 5 5 9" fill="none" stroke="#29a8e0" stroke-width="0.8"/></svg>
          www.tbk-plumbing.com.au
        </li>
        <li>
          <svg viewBox="0 0 10 10"><rect x="1" y="2" width="8" height="6" fill="none" stroke="#29a8e0" stroke-width="1"/><path d="M1 2 L5 5.5 L9 2" fill="none" stroke="#29a8e0" stroke-width="1"/></svg>
          rowan@tbk-plumbing.com.au
        </li>
      </ul>
    </div>
    <div class="accent-dot"></div>

    <p class="abn">ABN - 73 215 904 386</p>
  </section>

  <section class="card card--back" aria-label="Business card back">
    <div class="wordmark">
      <span class="wordmark__name">tbk</span>
      <span class="wordmark__tagline">plumbing services</span>
    </div>
  </section>
</main>
</body>
</html>
```